New Cryotherapy Business needs a Flyer Design

We are expanding our massage business located in Sydney with a Cryosauna. We need a flyer/brochure that explain what whole body cryotherapy is and all its benefits in a very simple way as we are the first cryotherapy business in Sydney and not many people knows what it is yet. We would like to see a design that use the color of our logo or shades of blue that comunicate freshness, innovation and health but also movement and sport performance. The flyer targets gym's members, athletes and also yoga/pilates goers with a focus on wellbeing and health.

Please find attached our logo (we actually prefer to use the logo/font in the banner adding the hand underneath the vitruvian man) and some examples of cryotherapy flyers with the information about the product/service we would like to include in the flyer. We would like also to include a section with special offer for new clients.

Target Market(s)

The flyer targets gym's members, athletes and also yoga/pilates goers with a focus on wellbeing and health.

Industry/Entity Type

Health And Wellness

Font styles to use
Sans Serif

Colors
f78f20
848484
c3c3c3
85acd3
0792cd
3176b5

Requirements
Must have
• logo, contact details, FAQs, About WBC, Benefits, Applications include, special offer for new clients section, pic of cryosauna with muscular guy, logos of "as seen on tv"

```html
<!DOCTYPE html>
<html lang="en">
<head>
<meta charset="utf-8">
<title>Whole Body Cryotherapy Brochure</title>
<link href="https://fonts.googleapis.com/css2?family=Anton&family=Marcellus&family=Roboto+Condensed:ital,wght@0,400;0,700;1,700&display=swap" rel="stylesheet">
<style>
:root{
  --ink:#0f1114;
  --panel:#16191d;
  --blue:#0792cd;
  --sky:#1ba7e4;
  --navy:#3176b5;
  --ice:#85acd3;
  --silver:#c3c3c3;
  --grey:#848484;
  --white:#ffffff;
}
*{margin:0;padding:0;box-sizing:border-box}
html,body{width:798px;height:1200px;overflow:hidden;background:var(--ink)}
body{font-family:"Roboto Condensed",sans-serif;color:var(--white)}
.sheet{position:relative;width:798px;height:1200px;overflow:hidden;background:var(--ink)}
.abs{position:absolute}
.photo{position:absolute}
.body-copy{font-weight:700;font-size:7.1px;line-height:1.62;text-transform:uppercase;text-align:center;color:var(--white)}
.hl{color:var(--sky)}

/* FAQ panel */
.faq-title{left:52px;top:88px;font-family:"Marcellus",serif;font-size:62px;color:var(--sky);letter-spacing:-1px}
.faq-title small{font-size:40px}
.faq-q{font-weight:700;font-size:9px;text-transform:uppercase;color:var(--sky);text-align:center;width:280px;left:0}
.faq-q span{color:var(--white)}
.faq-a{left:16px;width:250px}

/* contact strip */
.strip{left:300px;top:170px;width:198px;height:430px;background:linear-gradient(180deg,#0a7fd0,#1a9ae6 60%,#0c86d6)}
.tv-label{left:300px;top:194px;width:198px;text-align:center;font-weight:700;font-style:italic;font-size:10px}
.tv-board{left:338px;top:207px;width:102px;height:210px;background:var(--white);display:grid;grid-template-columns:repeat(3,1fr);grid-template-rows:repeat(5,1fr);gap:8px;padding:10px 8px}
.tv-board i{display:block;background:#2b2f36;border-radius:2px}
.tv-board i:nth-child(3n+2){background:#9aa3ad}
.tv-board i:nth-child(4n){background:#c94a3a}
.address{left:324px;top:430px;font-weight:700;font-size:9.6px;line-height:1.3;text-transform:uppercase}
.phone{left:324px;top:476px;font-size:15px;letter-spacing:1px}
.email{left:324px;top:508px;font-size:9.5px;font-weight:700}
.coupon{left:355px;top:525px;width:97px;height:67px;background:var(--white);padding:3px}
.coupon-in{border:1.5px dashed var(--blue);height:100%;background:var(--sky);text-align:center;color:var(--white);padding-top:4px}
.coupon-in b{display:block;font-size:9.5px;letter-spacing:.3px}
.coupon-in em{display:block;font-style:normal;font-size:6.2px;font-weight:700}
.coupon-in .price{font-size:18px;font-weight:700;line-height:1}
.coupon-in .price sup{font-size:8px}
.coupon-in .price small{font-size:5px;font-style:italic;font-weight:400}
.coupon-in .note{font-size:4.6px;font-style:italic;font-weight:400}

/* cover */
.brand{left:560px;top:18px;width:210px;text-align:center}
.brand-dot{display:inline-block;width:26px;height:26px;border:1.5px solid var(--white);border-radius:50%}
.brand-name{font-family:"Roboto Condensed",sans-serif;font-size:32px;letter-spacing:4px;line-height:1.1;color:var(--white)}
.brand-sub{font-size:6px;letter-spacing:.6px;color:var(--white)}
.cover-title{left:540px;top:210px;width:250px;text-align:center;font-family:"Anton",sans-serif;line-height:.98}
.cover-title .big{font-size:40px;color:#d8d8d8;display:block}
.cover-title .cryo{font-size:36px;display:block}
.cover-title .cryo b{color:var(--sky);font-weight:400}
.tagline{left:570px;top:362px;width:190px;text-align:center;font-size:15px;line-height:.95}
.tagline b{font-family:"Anton",sans-serif;font-size:32px;color:var(--sky);font-weight:400}
.book{left:540px;top:532px;width:254px;height:44px;border:1.5px solid var(--white);text-align:center;padding-top:5px}
.book p{font-weight:700;font-size:11.5px}
.book .url{font-size:12px;margin-top:2px}
.book svg{position:absolute;left:5px;top:23px}

/* about */
.about-title{left:0;top:732px;width:240px;text-align:center;font-weight:700;line-height:.95}
.about-title .w{font-size:27px;display:block}
.about-title .c{font-size:16px;display:block;font-weight:400;letter-spacing:.3px}
.about-title .a{font-size:15px;display:block;margin-top:3px}
.about-copy{left:12px;top:824px;width:252px}
.benefits-title{left:0;top:1068px;width:264px;text-align:center;font-weight:700;font-size:19px}
.benefits{left:0;top:1100px;width:262px;height:80px;background:var(--sky);display:flex;gap:6px;padding:3px 0 0 16px}
.benefits ul{list-style:none;font-size:6.6px;font-weight:700;line-height:1.42;text-transform:uppercase}
.benefits li::before{content:"\2714 ";}
.benefits small{font-size:3.8px}

/* applications */
.apps{left:296px;top:808px;width:212px;height:392px;background:linear-gradient(180deg,#0c87d8,#1a9be6)}
.apps-title{left:296px;top:822px;width:212px;text-align:center;font-weight:700;font-size:21px;letter-spacing:1.5px;border-bottom:1.5px solid var(--white);padding-bottom:1px}
.apps-list{left:296px;top:856px;width:212px;list-style:none;text-align:center;font-weight:700;font-style:italic;font-size:7.6px;text-transform:uppercase;line-height:18.1px}
.apps-list li::before{content:"\2714  ";}
.apps-list small{font-size:5.4px}
.badge{left:346px;top:1110px;width:94px;height:60px;background:var(--white);text-align:center;padding-top:2px}
.badge p{color:var(--blue);font-size:5.6px;font-weight:700;line-height:1.1}
.badge .marks{display:flex;justify-content:center;gap:6px;margin-top:5px}
.badge .marks i{width:14px;height:22px;background:var(--navy);display:block;border-radius:2px}
.badge .marks i:nth-child(2){background:#c0413b}

/* how it works */
.how-title{left:560px;top:1003px;width:210px;text-align:center;font-weight:700;font-size:14px}
.how-copy{left:540px;top:1022px;width:250px}
.logo-small{left:706px;top:622px;text-align:center}
.logo-small .brand-dot{width:14px;height:14px;border-width:1px}
.logo-small .n{font-size:15px;letter-spacing:2px;line-height:1.1}
.logo-small .s{font-size:3.2px}
</style>
</head>
<body>
<main class="sheet">

  <!-- top left: FAQ panel -->
  <div class="photo" role="img" aria-label="Dark frosted pine forest backdrop" style="left:0;top:0;width:300px;height:600px;background:radial-gradient(ellipse at 30% 20%,#3a3f44,#1a1d21 60%,#121417)"></div>
  <h1 class="abs faq-title">FAQ<small>s</small></h1>

  <h2 class="abs faq-q" style="top:218px">How do I feel after treatment<span>?</span></h2>
  <p class="abs body-copy faq-a" style="top:234px">Your external skin temperature warms up within five minutes of exiting the cryosauna. The immediate effects from each session typically last for six to eight hours. Cryotherapy stimulates the body to release endorphins, which are the hormones that make you feel good and energetic. Most clients report a better night's sleep after just one session!</p>

  <h2 class="abs faq-q" style="top:334px">Is it safe<span>?</span></h2>
  <p class="abs body-copy faq-a" style="top:350px">Yes. It has shown to be both safe and effective for a staggering variety of conditions and goals. Nitrogen is a non-toxic gas that makes up about 78% of the air we breathe. However, breathing pure nitrogen could cause fainting, due to the lack of oxygen. To prevent this, the cryosauna is designed to keep the patient's head above the chamber, and patients are instructed to breathe up room-air.</p>

  <h2 class="abs faq-q" style="top:465px;width:260px">Is it comfortable<span>?</span></h2>
  <p class="abs body-copy faq-a" style="top:479px;left:4px;width:250px">Where an ice bath has direct contact with the skin and can be painful, cryotherapy is a dry, indirect contact. Due to the session only being three minutes max, the session is very tolerable. Towards the end of the session, you may get a 'pins and needles' sensation, which disappears immediately after the treatment.</p>

  <svg class="abs" style="left:281px;top:432px" width="18" height="100" viewBox="0 0 18 100">
    <path d="M9 0a7 7 0 0 0-7 7c0 6 7 14 7 14s7-8 7-14a7 7 0 0 0-7-7z" fill="#1ba7e4"/>
    <circle cx="9" cy="7" r="2.6" fill="#16191d"/>
    <rect x="1.5" y="42" width="15" height="15" rx="3" fill="#e6e6e6"/>
    <path d="M6 45c-1 1-1 3 1 6s4 4 5 3l1-1-2-2-1 1c-1 0-3-2-3-3l1-1-2-2z" fill="#16191d"/>
    <rect x="1" y="78" width="16" height="11" fill="none" stroke="#e6e6e6" stroke-width="1.2"/>
    <path d="M1 78l8 6 8-6" fill="none" stroke="#e6e6e6" stroke-width="1.2"/>
  </svg>

  <!-- top centre -->
  <div class="photo" role="img" aria-label="Woman seen from behind holding her sore neck and shoulders, highlighted in red" style="left:300px;top:0;width:232px;height:182px;background:linear-gradient(180deg,#5a5e63,#a9a9a9 55%,#cfcfcf)"></div>
  <div class="abs strip"></div>
  <svg class="abs" style="left:220px;top:160px" width="320" height="40" viewBox="0 0 320 40">
    <path d="M0 40C60 14 150 4 320 10V0C150 -2 60 8 0 34z" fill="#1ba7e4"/>
    <path d="M80 40C140 20 220 14 312 16V22C220 20 150 26 80 40z" fill="#0a6fb8"/>
  </svg>
  <p class="abs tv-label">AS SEEN ON TV</p>
  <div class="abs tv-board" aria-label="Television features">
    <i></i><i></i><i></i><i></i><i></i><i></i><i></i><i></i><i></i><i></i><i></i><i></i><i></i><i></i><i></i>
  </div>
  <p class="abs address">Suite 12, 48 Harbour Lane<br>Elizabeth Bay NSW<br>2011 AU</p>
  <p class="abs phone">(0400 000 123)</p>
  <p class="abs email">INFO@NORDACRYO.COM.AU</p>
  <div class="abs coupon">
    <div class="coupon-in">
      <b>SPECIAL OFFER</b>
      <em>INTRODUCTORY SESSION</em>
      <span class="price"><sup>$</sup>75 <small>(Regular Price $90)</small></span>
      <div class="note">(for new WBC clients only)</div>
    </div>
  </div>

  <!-- top right: cover -->
  <div class="photo" role="img" aria-label="Cryosauna chamber lit from above on a dark stage" style="left:540px;top:90px;width:258px;height:430px;background:radial-gradient(ellipse at 50% 25%,#8c8f93,#3a3d41 45%,#16191d 80%)"></div>
  <div class="abs brand">
    <span class="brand-dot"></span>
    <div class="brand-name">NORDA</div>
    <div class="brand-sub">NORDIC HEALING ARTS STUDIO</div>
  </div>
  <h2 class="abs cover-title">
    <span class="big">WHOLE<br>BODY</span>
    <span class="cryo"><b>CRYO</b>THERAPY</span>
  </h2>
  <p class="abs tagline">JUST <b>3</b> MINUTES<br>FOR WHOLE BODY<br>RECOVERY</p>
  <div class="abs book">
    <p>BOOK YOUR APPOINTMENT TODAY</p>
    <p class="url">WWW.<span class="hl">NORDACRYO</span>.COM</p>
    <svg width="16" height="16" viewBox="0 0 16 16" fill="none" stroke="#fff" stroke-width="1"><circle cx="8" cy="8" r="7"/><ellipse cx="8" cy="8" rx="3" ry="7"/><path d="M1 8h14M2.5 4h11M2.5 12h11"/></svg>
  </div>

  <!-- bottom left: about -->
  <div class="photo" role="img" aria-label="Swimmer doing butterfly stroke splashing through dark water" style="left:0;top:600px;width:300px;height:170px;background:linear-gradient(180deg,#121417,#4c5257 50%,#1b1e22)"></div>
  <svg class="abs" style="left:60px;top:612px" width="110" height="60" viewBox="0 0 110 60">
    <rect x="14" y="0" width="16" height="16" fill="#1ba7e4"/>
    <rect x="54" y="14" width="30" height="30" fill="#1ba7e4" opacity=".9"/>
    <rect x="0" y="34" width="22" height="22" fill="#0792cd"/>
    <rect x="38" y="30" width="14" height="14" fill="#0792cd"/>
    <rect x="86" y="40" width="18" height="18" fill="#1ba7e4"/>
  </svg>
  <h2 class="abs about-title">
    <span class="w">WHOLE<br>BODY</span>
    <span class="c"><span class="hl">CRYO</span>THERAPY</span>
    <span class="a">ABOUT:</span>
  </h2>
  <p class="abs body-copy about-copy" style="font-size:7.6px;line-height:1.72">WBC (<span class="hl">Whole Body Cryotherapy</span>) was first utilized in Japan in the early 1970's by Dr. Tanabe to treat rheumatoid arthritis and inflammatory join diseases. Proving extremely effective, WBC quickly gained notoriety for that specific issue, but also to treat systemic inflammation processes throughout the body. Now elite athletes and pro teams have adopted WBC for muscle and injury recovery and as a powerful treatment to decrease recovery time and increase athletic performance and boost the body's metabolic rate. WBC is becoming worldwide well documented as being used for the daily management of pain, inflammation, energy, and stress related conditions. <span class="hl">NordaCryo</span> is one of the first few centres opened in Sydney aiming for the most safe, effective, and affordable treatments available to the public.</p>

  <h2 class="abs benefits-title">BENIFITS</h2>
  <div class="abs benefits">
    <ul>
      <li>Pain management</li><li>Rapid muscle recovery</li><li>Injury therapy</li><li>Performance enhancement</li><li>Increased energy levels</li><li>Increased libido</li><li>Sleep better</li><li>Better mood</li>
    </ul>
    <ul>
      <li>Metabolic &amp; immunity boost</li><li>Caloric burn - <small>burn up to 800 calories</small></li><li>Anti-aging</li><li>Skin rejuvenation</li><li>Improved skin elasticity</li><li>Increased collagen production</li><li>Cellulite reduction</li><li>And much more</li>
    </ul>
  </div>

  <!-- bottom centre: applications -->
  <div class="photo" role="img" aria-label="Open cryosauna doors with quilted silver lining seen from above" style="left:240px;top:600px;width:292px;height:218px;background:radial-gradient(ellipse at 50% 40%,#f2f2f2,#b9b9b9 50%,#3a3d41 85%)"></div>
  <div class="abs apps"></div>
  <h2 class="abs apps-title">APPLICATIONS</h2>
  <ul class="abs apps-list">
    <li>Athletic performance</li>
    <li>Athletic recovery</li>
    <li>Postsurgical recovery</li>
    <li>Musculoskeletal injuries</li>
    <li>Osteoarthritis - rheumatoid arthritis</li>
    <li>Osteoarthritis - multiple sclerosis</li>
    <li>Fibromyalgia - <small>chronic fatigue syndrome</small></li>
    <li>Depression &amp; mood disorders</li>
    <li>Weight management</li>
    <li>Degenerative diseases of joints &amp; spine</li>
    <li>Phantom pain - chronic pain syndrome</li>
    <li>Autoimmune <small>and other inflammatory disorders</small></li>
    <li>Skin disorders <small>such as dermatitis and psoriasis</small></li>
  </ul>
  <div class="abs badge">
    <p>SERVING PRO ATHLETES<br>SINCE 2009</p>
    <div class="marks"><i></i><i></i><i></i><i></i></div>
  </div>

  <!-- bottom right: how it works -->
  <div class="photo" role="img" aria-label="Athletic man in white shorts and gloves stepping out of a misty cryosauna" style="left:556px;top:606px;width:242px;height:394px;background:radial-gradient(ellipse at 55% 60%,#b9b9b9,#5b5f63 45%,#1b1e22 80%)"></div>
  <div class="abs logo-small">
    <span class="brand-dot"></span>
    <div class="n">NORDA</div>
    <div class="s">NORDIC HEALING ARTS STUDIO</div>
  </div>
  <h2 class="abs how-title">&#10004; HOW IT WORKS:</h2>
  <p class="abs body-copy how-copy" style="font-size:7.4px;line-height:1.5">With <span class="hl">WBC</span>, the body is exposed to ultra-low temperatures (<span class="hl">-150°C</span> to <span class="hl">-190°C</span>) for less than 3 minutes. Extreme cold stimulates skin sensors, activating a central nervous system (CNS) response prompting the brain to transmit messages throughout the body. This causes the release of endorphins, the body's natural pain inhibitors and mood elevators, while the enhanced circulation activity (blood movement into and out of the core) decreases inflammation by clearing toxins and metabolic waste with a supply of oxygen and nutrient enriched blood to stimulate cellular regeneration (faster healing) promoting an overall better health. The body's natural anti-inflammatory reaction to extreme cold is pain reduction.</p>

</main>
</body>
</html>
```